Plakat-Design für Vereinsfest
Zielgruppe
Unser Verein veranstaltet jedes Jahr im August das Vereinsfest 'Mühlentanz', das in einem kleinen Wäldchen innerhalb des Heimatortes stattfindet. Am Samstag und Sonntag sorgen verschiedene Musikgruppen für Unterhaltung. Es soll ein Veranstaltungsplakat gestaltet werden, dass sich an die Vorgaben (siehe unten) hält und die Veranstaltung bewirbt.
Zielgruppe sind Bürger des Heimatortes.
Aufgabenstellung
Das Vereinslogo ist beigefügt und sollte prominent auf dem Plakat vertreten sein, Logo und Schriftzug können auch getrennt oder anders angeordnet werden. Der Veranstaltungstitel lautet "Mühlentanz", es findet am 20. und 21. August "Am Rinkelsteig" (Veranstaltungsort) statt.
Programmpunkte: Samstag: Musikalische Unterhaltung mit den Hopfenbläsern; Sonntag: Musikalische Unterhaltung mit den Kieselgrubenrabauken
Uhrzeiten sollten enthalten sein:
Beginn Samstag: ab 15 Uhr
Beginn Sonntag: ab 10 Uhr
Das Plakat soll gut leserlich auch aus der Entfernung sein, da es an Straßen plakatiert wird.
Das Plakat soll für spätere Jahre editierbar sein.
Schriftart im Logo: Californian FB Bold (muss aber nicht auf andere Textelemente angewendet werden). Das Plakat soll in DIN A2 gedruckt werden. Die Webadresse sollte auf dem Plakat stehen.

```html
<!DOCTYPE html>
<html lang="de">
<head>
<meta charset="utf-8">
<title>Mühlentanz – Plakat</title>
<link href="https://fonts.googleapis.com/css2?family=Abril+Fatface&family=Libre+Caslon+Text:wght@400;700&display=swap" rel="stylesheet">
<style>
  :root{
    --backdrop:#e9e8e6;
    --paper:#f4f3f1;
    --blue:#175a85;
    --navy:#1f2a6b;
    --seal:#8fa6d8;
    --ink:#444444;
    --box:#4b4b4b;
    --white:#ffffff;
  }
  *{box-sizing:border-box;margin:0;padding:0}
  html,body{width:1200px;height:1178px;overflow:hidden;background:var(--backdrop)}
  body{font-family:"Libre Caslon Text",Georgia,serif}
  .poster{
    position:absolute;left:211px;top:39px;width:778px;height:1100px;
    background:var(--paper);box-shadow:0 2px 10px rgba(0,0,0,.12);
  }
  .frame-lines{position:absolute;inset:0}
  .corner{position:absolute;width:104px;height:104px}
  .corner--tl{left:36px;top:36px}
  .corner--tr{right:36px;top:36px}
  .corner--bl{left:36px;bottom:36px}
  .corner--br{right:36px;bottom:36px}
  .club{position:absolute;left:170px;top:58px;display:flex;align-items:center;gap:18px}
  .club__mark{width:132px;height:132px}
  .club__name{color:var(--navy);font-weight:400;line-height:1.02}
  .club__name .small{font-size:16px;display:block;padding-left:44px}
  .club__name .big{font-size:34px;display:block}
  .title{
    position:absolute;left:0;right:0;top:240px;text-align:center;
    font-family:"Abril Fatface",Georgia,serif;color:var(--blue);
    font-size:92px;letter-spacing:-1px;transform:scaleY(1.55);transform-origin:top center;
    line-height:1;
  }
  .dateband{
    position:absolute;left:58px;right:58px;top:438px;height:104px;background:var(--blue);
    color:var(--white);text-align:center;
  }
  .dateband__date{font-weight:700;font-size:46px;line-height:1;padding-top:14px}
  .dateband__place{font-size:32px;line-height:1;margin-top:8px}
  .band-orn{position:absolute;width:30px;height:30px}
  .program{position:absolute;left:0;right:0;text-align:center}
  .program__day{color:var(--ink);font-weight:700;font-size:28px;letter-spacing:.5px;line-height:1.1}
  .program__act{color:var(--blue);font-weight:700;font-size:22px;line-height:1.38;margin-top:2px}
  .program--sat{top:578px}
  .program--sun{top:736px}
  .times{
    position:absolute;left:168px;width:442px;top:880px;height:96px;background:var(--box);
    color:var(--white);text-align:center;font-size:26px;line-height:1.25;padding-top:14px;
  }
  .web{position:absolute;left:0;right:0;top:1000px;text-align:center;color:var(--ink);font-weight:700;font-size:30px}
</style>
</head>
<body>
<main class="poster">
  <svg class="frame-lines" viewBox="0 0 778 1100" aria-hidden="true">
    <rect x="16" y="16" width="746" height="1068" fill="none" stroke="var(--blue)" stroke-width="4"/>
    <rect x="25" y="25" width="728" height="1050" fill="none" stroke="var(--blue)" stroke-width="1.5"/>
  </svg>

  <svg class="corner corner--tl" role="img" aria-label="Rankenornament Ecke oben links"><path d="M0 0H104L0 104Z" fill="var(--blue)" opacity=".16"/></svg>
  <svg class="corner corner--tr" role="img" aria-label="Rankenornament Ecke oben rechts"><path d="M0 0H104V104Z" fill="var(--blue)" opacity=".16"/></svg>
  <svg class="corner corner--bl" role="img" aria-label="Rankenornament Ecke unten links"><path d="M0 0V104H104Z" fill="var(--blue)" opacity=".16"/></svg>
  <svg class="corner corner--br" role="img" aria-label="Rankenornament Ecke unten rechts"><path d="M104 0V104H0Z" fill="var(--blue)" opacity=".16"/></svg>

  <header class="club">
    <svg class="club__mark" viewBox="0 0 132 132" aria-hidden="true"><circle cx="66" cy="66" r="64" fill="var(--seal)"/></svg>
    <p class="club__name">
      <span class="small">Historischer</span>
      <span class="big">Mühlenverein und</span>
      <span class="big">Trachtengruppe</span>
      <span class="big">Lindach e.V.</span>
    </p>
  </header>

  <h1 class="title">MÜHLENTANZ</h1>

  <section class="dateband">
    <svg class="band-orn" style="left:6px;top:6px" role="img" aria-label="Zierornament"><rect width="30" height="30" fill="var(--white)" opacity=".15"/></svg>
    <svg class="band-orn" style="right:6px;top:6px" role="img" aria-label="Zierornament"><rect width="30" height="30" fill="var(--white)" opacity=".15"/></svg>
    <svg class="band-orn" style="left:6px;bottom:6px" role="img" aria-label="Zierornament"><rect width="30" height="30" fill="var(--white)" opacity=".15"/></svg>
    <svg class="band-orn" style="right:6px;bottom:6px" role="img" aria-label="Zierornament"><rect width="30" height="30" fill="var(--white)" opacity=".15"/></svg>
    <p class="dateband__date">20. - 21. August</p>
    <p class="dateband__place">“Am Rinkelsteig”</p>
  </section>

  <section class="program program--sat">
    <h2 class="program__day">SAMSTAG:</h2>
    <p class="program__act">Musikalische Unterhaltung mit den<br>Hopfenbläsern</p>
  </section>

  <section class="program program--sun">
    <h2 class="program__day">SONNTAG:</h2>
    <p class="program__act">Musikalische Unterhaltung mit den<br>Kieselgrubenrabauken</p>
  </section>

  <section class="times">
    <p>Beginn Samstag: ab 15 Uhr</p>
    <p>Beginn Sonntag: ab 10 Uhr</p>
  </section>

  <p class="web">www.muehlenverein-lindach.de</p>
</main>
</body>
</html>
```